Essential Oil 15ml - package of 6

Design of a box of 6 different essential oils.
+ design of the bottle stickers
My bottles are 15ml clear blue glass.

The pictures attached are my competitors...

Target Market(s)

TERVIK USA

Font styles to use
Serif

Requirements
Must have
• Our logo + "essential oil" and type (lavender, eucalyptus etc....)
• 15ml - 0.50 fl.oz.
• special color for the oil type.

```html
<!DOCTYPE html>
<html lang="en">
<head>
<meta charset="utf-8">
<title>Oren Vale – Essential Oil Labels</title>
<link rel="stylesheet" href="https://fonts.googleapis.com/css2?family=Marcellus&family=Delius&family=Questrial&display=swap">
<style>
  :root {
    --sheet-gap: #ffffff;
    --label-base: #8a6542;
    --label-light: #9a7450;
    --label-dark: #7a5636;
    --ink: #111111;
    --ink-soft: #2b1c0f;
    --gold-rule: #c8933f;
    --tea-tree: #4b4b24;
    --sweet-orange: #7c3612;
    --rosemary: #2f0f13;
    --peppermint: #213c4c;
    --lavender: #513734;
    --eucalyptus: #265238;
  }
  * { box-sizing: border-box; margin: 0; padding: 0; }
  html, body { width: 1200px; height: 602px; overflow: hidden; background: var(--sheet-gap); }
  .label-sheet {
    width: 1200px; height: 602px;
    display: grid;
    grid-template-columns: 1fr 1fr;
    grid-template-rows: repeat(3, 1fr);
    gap: 2px;
    background: var(--sheet-gap);
  }
  .label {
    position: relative;
    overflow: hidden;
    background: radial-gradient(ellipse at 50% 40%, var(--label-light), var(--label-base) 55%, var(--label-dark));
  }
  .brand-mark {
    position: absolute; left: 50%; top: 12px;
    width: 46px; height: 46px; margin-left: -23px;
    border-radius: 50%;
    background: var(--ink);
  }
  .brand-name {
    position: absolute; left: 0; right: 0; top: 62px;
    text-align: center;
    font-family: "Marcellus", serif;
    font-size: 31px; line-height: 34px;
    color: var(--ink);
  }
  .oil-band {
    position: absolute; left: 0; right: 0; top: 99px; height: 40px;
    border-top: 2px solid var(--gold-rule);
    border-bottom: 2px solid var(--gold-rule);
    display: flex; align-items: center; justify-content: center;
    font-family: "Delius", cursive;
    font-size: 22px; letter-spacing: 1px;
    color: var(--ink);
  }
  .oil-band--tea-tree { background: var(--tea-tree); }
  .oil-band--sweet-orange { background: var(--sweet-orange); }
  .oil-band--rosemary { background: var(--rosemary); }
  .oil-band--peppermint { background: var(--peppermint); }
  .oil-band--lavender { background: var(--lavender); }
  .oil-band--eucalyptus { background: var(--eucalyptus); }
  .oil-type {
    position: absolute; left: 0; right: 0; top: 148px;
    text-align: center;
    font-family: "Questrial", sans-serif;
    font-size: 17px; color: var(--ink-soft);
  }
  .oil-volume {
    position: absolute; left: 0; right: 0; top: 175px;
    text-align: center;
    font-family: "Questrial", sans-serif;
    font-size: 12px; color: var(--ink-soft);
  }
</style>
</head>
<body>
<main class="label-sheet">
  <section class="label">
    <span class="brand-mark"></span>
    <p class="brand-name">Oren Vale</p>
    <p class="oil-band oil-band--tea-tree">Tea Tree</p>
    <p class="oil-type">Pure Essential Oil</p>
    <p class="oil-volume">15ml (0.50 fl.oz)</p>
  </section>
  <section class="label">
    <span class="brand-mark"></span>
    <p class="brand-name">Oren Vale</p>
    <p class="oil-band oil-band--sweet-orange">SWEET ORANGE</p>
    <p class="oil-type">Pure Essential Oil</p>
    <p class="oil-volume">15ml (0.50 fl.oz)</p>
  </section>
  <section class="label">
    <span class="brand-mark"></span>
    <p class="brand-name">Oren Vale</p>
    <p class="oil-band oil-band--rosemary">ROSEMARY</p>
    <p class="oil-type">Pure Essential Oil</p>
    <p class="oil-volume">15ml (0.50 fl.oz)</p>
  </section>
  <section class="label">
    <span class="brand-mark"></span>
    <p class="brand-name">Oren Vale</p>
    <p class="oil-band oil-band--peppermint">PEPPERMINT</p>
    <p class="oil-type">Pure Essential Oil</p>
    <p class="oil-volume">15ml (0.50 fl.oz)</p>
  </section>
  <section class="label">
    <span class="brand-mark"></span>
    <p class="brand-name">Oren Vale</p>
    <p class="oil-band oil-band--lavender">LAVENDER</p>
    <p class="oil-type">Pure Essential Oil</p>
    <p class="oil-volume">15ml (0.50 fl.oz)</p>
  </section>
  <section class="label">
    <span class="brand-mark"></span>
    <p class="brand-name">Oren Vale</p>
    <p class="oil-band oil-band--eucalyptus">EUCALYLPTUS</p>
    <p class="oil-type">Pure Essential Oil</p>
    <p class="oil-volume">15ml (0.50 fl.oz)</p>
  </section>
</main>
</body>
</html>
```